Bramblewood Card Company Business Cards

We are a trading card store with Glimmorax, sports and other TCG cards, we need a business card design that encompasses a clean cut, modern style with a retro flare. website is bramblewoodcardco.com for reference. Can utilize a comic book era feel or a more modern outdoor feel to utilize the "Pacific Northwest" elements of tress, mountains, etc.

Industry/Entity Type

Trading cards and collectibles

Contact Information for Business Card

business name, email address, phone number, name, owner job title

Font styles to use
Sans Serif

```html
<!DOCTYPE html>
<html lang="en">
<head>
<meta charset="utf-8">
<title>Bramblewood Card Company – Business Card</title>
<link href="https://fonts.googleapis.com/css2?family=Montserrat:wght@400;500;700&display=swap" rel="stylesheet">
<style>
  :root {
    --stage: #2a2b2d;
    --card: #1e1f21;
    --card-back: #191a1c;
    --accent: #1fbfe0;
    --stripe: #6b6c6e;
    --ink: #f2f2f2;
    --muted: #bdbdbd;
  }
  html, body {
    margin: 0;
    width: 1200px;
    height: 801px;
    overflow: hidden;
    background: var(--stage);
    font-family: "Montserrat", Arial, sans-serif;
  }
  .stage {
    position: relative;
    width: 1200px;
    height: 801px;
  }
  .card {
    position: absolute;
    top: 246px;
    width: 540px;
    height: 309px;
    border-radius: 18px;
    overflow: hidden;
    box-shadow: 0 18px 40px rgba(0,0,0,.55);
  }
  .card--front { left: 40px; background: var(--card); }
  .card--back { left: 620px; background: var(--card-back); }

  .front-wave {
    position: absolute;
    inset: 0;
  }
  .brand-name {
    position: absolute;
    top: 34px;
    right: 32px;
    display: flex;
    align-items: center;
    gap: 12px;
    color: var(--ink);
    font-weight: 700;
    font-size: 18px;
    line-height: 1.2;
    letter-spacing: .06em;
    text-transform: uppercase;
    text-align: right;
  }
  .brand-name .brand-dot {
    width: 14px;
    height: 14px;
    background: var(--accent);
    flex: none;
  }
  .name-marker {
    position: absolute;
    left: 0;
    top: 44px;
    width: 14px;
    height: 30px;
    background: var(--accent);
  }
  .identity {
    position: absolute;
    left: 30px;
    top: 38px;
  }
  .identity .person {
    margin: 0;
    color: var(--accent);
    font-weight: 700;
    font-size: 23px;
    letter-spacing: .04em;
    text-transform: uppercase;
  }
  .identity .role {
    margin: 2px 0 0;
    color: var(--ink);
    font-size: 14px;
  }
  .address {
    position: absolute;
    left: 30px;
    top: 118px;
    margin: 0;
    color: var(--ink);
    font-size: 13.5px;
    line-height: 1.45;
    font-style: normal;
  }
  .contacts {
    position: absolute;
    left: 30px;
    top: 178px;
    margin: 0;
    padding: 0;
    list-style: none;
    color: var(--ink);
    font-size: 13.5px;
  }
  .contacts li {
    display: flex;
    align-items: center;
    gap: 8px;
    height: 22px;
  }
  .contacts svg { width: 12px; height: 12px; fill: var(--accent); }

  .back-pattern {
    position: absolute;
    inset: 0;
    background: linear-gradient(135deg, #1a1b1d 0%, #2b2c2e 55%, #4a4b4d 100%);
  }
</style>
</head>
<body>
<main class="stage">

  <section class="card card--front" aria-label="Business card front">
    <svg class="front-wave" viewBox="0 0 540 309" preserveAspectRatio="none" aria-hidden="true">
      <path fill="var(--stripe)" d="M150 309 C260 300 300 225 360 185 C420 145 480 125 540 110 L540 309 Z"/>
      <path fill="var(--accent)" d="M175 309 C285 302 325 245 385 200 C445 155 495 140 540 130 L540 309 Z"/>
    </svg>

    <div class="brand-name"><span class="brand-dot"></span><span>Bramblewood<br>Card Company</span></div>

    <span class="name-marker"></span>
    <header class="identity">
      <h1 class="person">Dorian Pell</h1>
      <p class="role">CEO/Founder</p>
    </header>

    <address class="address">P.O. Box 3870 Lane<br>Cedar Falls WA 9031</address>

    <ul class="contacts">
      <li>
        <svg viewBox="0 0 24 24"><path d="M6.6 10.8a15.1 15.1 0 0 0 6.6 6.6l2.2-2.2a1 1 0 0 1 1-.25 11.4 11.4 0 0 0 3.6.57 1 1 0 0 1 1 1V20a1 1 0 0 1-1 1A17 17 0 0 1 3 4a1 1 0 0 1 1-1h3.5a1 1 0 0 1 1 1c0 1.25.2 2.45.57 3.57a1 1 0 0 1-.25 1z"/></svg>
        (555) 214 0376
      </li>
      <li>
        <svg viewBox="0 0 24 24"><path d="M2 5h20v14H2z" fill="var(--accent)"/><path d="M2 5l10 8 10-8" fill="none" stroke="var(--card)" stroke-width="2"/></svg>
        info@bramblewoodcardco.com
      </li>
      <li>
        <svg viewBox="0 0 24 24"><circle cx="12" cy="12" r="10"/><path d="M2 12h20M12 2c3 3 3 17 0 20M12 2c-3 3-3 17 0 20" fill="none" stroke="var(--card)" stroke-width="1.5"/></svg>
        www.bramblewoodcardco.com
      </li>
    </ul>
  </section>

  <section class="card card--back" aria-label="Business card back">
    <div class="back-pattern" role="img" aria-label="Repeating tonal brand mark pattern in dark and mid greys across the card back"></div>
  </section>

</main>
</body>
</html>
```